Los Brava Dip – CPG Website with WordPress - Store Locator: WP Maps plugin

Larkfield Food Company is a startup consumer packaged goods (CPG) brand launching its flagship product line — Los Brava Dip. We’re seeking a talented web designer to create a bold, professional, mobile-optimized website using WordPress with a WP Maps store locator to help customers find local retailers.

Our goal is to build a strong online presence that supports both retail growth and direct-to-consumer sales.

See Los Brava _Website_Design_Brief word document.

The website URL is https://losbravadip.example/

Target Market(s)

Consumers of gourmet salsa

Industry/Entity Type

Consumer Packaged Goods - Salsa manufacturer.

Coding

Coded - Design and coding required

Number of Pages Required

5+ page

Requirements
Must have
• The design of the Los Brava Dip website shall emulate the clean, polished aesthetic of Fennigo.example.

```html
<!DOCTYPE html>
<html lang="en">
<head>
<meta charset="utf-8">
<title>Los Brava Dip</title>
<link href="https://fonts.googleapis.com/css2?family=Montserrat:wght@400;500;600;700&family=Playfair+Display:wght@900&display=swap" rel="stylesheet">
<style>
:root{
  --red:#c8202b;
  --red-dark:#a5161f;
  --green:#6aa53a;
  --green-btn:#4f8a2e;
  --yellow:#f5b800;
  --ink:#1b1b1b;
  --muted:#444;
  --white:#fff;
  --footer-line:#ddd;
}
*{box-sizing:border-box;margin:0;padding:0}
html,body{width:1200px;height:2791px;overflow:hidden;background:var(--white)}
body{font-family:'Montserrat',sans-serif;color:var(--ink);position:relative}
.abs{position:absolute}
.heading{font-family:'Playfair Display',serif;font-weight:900;text-transform:uppercase;text-align:center;left:0;width:1200px;letter-spacing:.5px}

.top-bar{top:0;left:0;width:1200px;height:26px;background:var(--red);color:var(--white);font-size:12px;font-weight:700;text-align:center;line-height:26px}
.site-header{top:26px;left:0;width:1200px;height:76px;background:var(--white)}
.nav-link{top:34px;font-size:12px;font-weight:600;text-transform:uppercase;letter-spacing:.2px}
.brand{top:20px;left:520px;width:160px;text-align:center;font-size:28px;font-weight:700;color:var(--red)}
.btn-login{top:22px;left:860px;width:72px;height:34px;border:1.5px solid #333;border-radius:5px;font-size:12px;font-weight:600;text-align:center;line-height:31px}
.btn-contact{top:22px;left:941px;width:103px;height:34px;background:var(--red);color:var(--white);border-radius:5px;font-size:12px;font-weight:700;text-align:center;line-height:34px}
.cart{top:26px;left:1054px;width:27px;height:27px;border:1.5px solid #333;border-radius:50%}

.hero{top:102px;left:0;width:1200px;height:548px;background:linear-gradient(160deg,#5c8a2a 0%,#b23423 35%,#c0542a 60%,#7a4a2a 100%)}
.hero-title{top:190px;font-size:44px;color:var(--white);text-shadow:0 2px 6px rgba(0,0,0,.5)}
.hero-title span{color:#ffe62e}
.hero-jars{top:318px;left:365px;width:515px;height:330px;background:linear-gradient(90deg,#d9412a,#7fb33b 50%,#f0862a);border-radius:40px 40px 20px 20px;opacity:.9}

.section-title-dark{color:var(--ink);font-size:34px}
.product-card{top:761px;width:303px;height:394px;border-radius:4px;text-align:center}
.product-card.natural{left:126px;background:linear-gradient(#fff,#fdf0cf);border:1px solid #f2c97a}
.product-card.verde{left:450px;background:linear-gradient(#fff,#e3f2d6);border:1px solid #9bcd80}
.product-card.habanero{left:775px;background:linear-gradient(#fff,#f7d3d6);border:1px solid #e98a91}
.product-shot{position:absolute;top:38px;left:36px;width:230px;height:220px;border-radius:10px}
.natural .product-shot{background:radial-gradient(circle,#f3a13a,#fbe6bd 70%)}
.verde .product-shot{background:radial-gradient(circle,#8fbf4a,#e6f2d8 70%)}
.habanero .product-shot{background:radial-gradient(circle,#d8322e,#f8dada 70%)}
.product-name{position:absolute;top:283px;left:0;width:100%;font-size:15px;font-weight:500;line-height:19px}
.product-name b{font-size:19px;font-weight:700;display:block}
.shop-btn{position:absolute;top:335px;left:99px;width:105px;height:34px;border-radius:4px;color:var(--white);font-size:13px;font-weight:700;line-height:34px}
.natural .shop-btn{background:var(--yellow)}
.verde .shop-btn{background:var(--green-btn)}
.habanero .shop-btn{background:var(--red)}
.arrow{width:18px;height:18px;border-radius:50%;background:#222}
.arrow.light{background:#e9e9e9}

.reviews-band{top:1203px;left:0;width:1200px;height:380px;background:linear-gradient(120deg,#5e9a2e,#79b342 50%,#5a942b)}
.section-title-light{color:var(--white);font-size:34px}
.review-card{top:1325px;width:225px;height:215px;background:var(--white);border-radius:3px;padding:22px 17px}
.reviewer{display:flex;align-items:center;gap:8px;margin-bottom:14px}
.avatar{width:30px;height:30px;border-radius:50%;background:#8a93a6}
.reviewer-name{font-size:11px;font-weight:600}
.stars{color:var(--yellow);font-size:12px;letter-spacing:1px;line-height:12px}
.review-text{font-size:11px;line-height:16.3px;color:var(--muted)}

.recipe-card{top:1693px;width:468px;height:325px;background:var(--yellow)}
.recipe-photo{position:absolute;top:9px;left:9px;width:214px;height:307px;border:4px solid var(--white)}
.recipe-photo.beef-rice{background:linear-gradient(150deg,#c9c9c9,#b5542a 55%,#7a2d14)}
.recipe-photo.salsa-beef{background:linear-gradient(150deg,#3b3b3b,#6f9b3a 40%,#c7682f 70%,#efefef)}
.recipe-title{position:absolute;top:38px;left:246px;font-size:21px;font-weight:600;line-height:23px;color:var(--ink)}
.recipe-text{position:absolute;top:98px;left:246px;width:213px;font-size:11px;line-height:16.3px;color:#3a2a00}
.recipe-btn{position:absolute;top:264px;left:247px;width:124px;height:34px;background:var(--red);color:var(--white);font-size:13px;font-weight:700;text-align:center;line-height:34px;border-radius:4px}

.insta-tile{top:2137px;width:169px;height:161px}

.signup-band{top:2320px;left:0;width:1200px;height:238px;background:var(--red)}
.signup-field{top:2441px;left:373px;width:441px;height:43px;background:var(--white);border-radius:4px}
.signup-field span{position:absolute;left:18px;top:14px;font-size:12px}
.subscribe{position:absolute;top:4px;right:4px;width:104px;height:35px;background:#58b01c;color:var(--white);font-size:14px;font-weight:700;text-align:center;line-height:35px;border-radius:4px}

.footer-brand{top:2636px;left:124px;font-size:32px;font-weight:700;color:var(--red)}
.footer-divider{top:2608px;width:1px;height:154px;background:var(--footer-line)}
.footer-head{top:2609px;font-family:'Playfair Display',serif;font-weight:900;font-size:15px;letter-spacing:.5px}
.footer-list{list-style:none;font-size:10px;line-height:20px;top:2644px}
.footer-item{display:flex;align-items:center;gap:9px;height:28px}
.icon-dot{width:17px;height:17px;border-radius:50%;background:#111}
.bottom-bar{top:2762px;left:0;width:1200px;height:29px;background:#111;color:var(--white);font-size:9px;text-align:center;line-height:29px}
</style>
</head>
<body>

<div class="abs top-bar">Free Shipping On All Orders!</div>

<header class="abs site-header">
  <a class="abs nav-link" style="left:123px">Featured Product</a>
  <a class="abs nav-link" style="left:279px">Where To Buy</a>
  <a class="abs nav-link" style="left:402px">Recipes</a>
  <div class="abs brand">Los Brava</div>
  <a class="abs nav-link" style="left:705px">About</a>
  <a class="abs nav-link" style="left:778px">Reviews</a>
  <div class="abs btn-login">LOGIN</div>
  <div class="abs btn-contact">CONTACT US</div>
  <div class="abs cart"></div>
</header>

<section class="abs hero" role="img" aria-label="Red chillies, tortilla chips and a bowl of salsa behind three jars of Los Brava Dip"></section>
<h1 class="abs heading hero-title"><span>Spice</span> Up Your Meals!</h1>
<div class="abs hero-jars" role="img" aria-label="Habanero, Verde and All Natural jars of Los Brava Dip"></div>

<h2 class="abs heading section-title-dark" style="top:698px">Featured Product</h2>
<div class="abs arrow" style="top:958px;left:81px"></div>
<div class="abs product-card natural"><div class="product-shot" role="img" aria-label="All Natural jar with red chilli and flakes"></div><div class="product-name">Los Brava Sal<b>Allnatural</b></div><div class="shop-btn">Shop Now</div></div>
<div class="abs product-card verde"><div class="product-shot" role="img" aria-label="Verde jar with green pepper and herbs"></div><div class="product-name">Los Brava Sal<b>Verde</b></div><div class="shop-btn">Shop Now</div></div>
<div class="abs product-card habanero"><div class="product-shot" role="img" aria-label="Habanero jar with red chillies"></div><div class="product-name">Los Brava Sal<b>Habanero</b></div><div class="shop-btn">Shop Now</div></div>
<div class="abs arrow" style="top:958px;left:1103px"></div>

<section class="abs reviews-band" role="img" aria-label="Green peppers background"></section>
<h2 class="abs heading section-title-light" style="top:1258px">Customer Reviews</h2>
<div class="abs arrow light" style="top:1423px;left:81px"></div>
<div class="abs review-card" style="left:124px"><div class="reviewer"><div class="avatar"></div><div><div class="reviewer-name">Dana Ortiz</div><div class="stars">★★★★★</div></div></div><p class="review-text">“Very good, and I’m a salsa snob!” Sed laoreet, arcu eu volutpat vulputate, urna nisi elementum nunc, in gravida libero arcu sit amet neque. Fusce et ultrices nisi. Suspendisse eu suscipit odio. Nulla non rhoncus erat in vulputate nisi.</p></div>
<div class="abs review-card" style="left:367px"><div class="reviewer"><div class="avatar"></div><div><div class="reviewer-name">Dana Ortiz</div><div class="stars">★★★★★</div></div></div><p class="review-text">“Very nice overall. I cook a lot s I often make my own, but this is great” Sed laoreet, arcu eu volutpat vulputate, urna nisi elementum nunc, in gravida libero arcu sitamet neque.</p></div>
<div class="abs review-card" style="left:611px"><div class="reviewer"><div class="avatar"></div><div><div class="reviewer-name">Dana Ortiz</div><div class="stars">★★★★★</div></div></div><p class="review-text">“Really good flavor. Sed laoreet, arcu eu volutpat vulputate, urna nisi elementum nunc, in gravida libero arcu sit amet neque. Fusce et ultrices nisi. Suspendisse eu suscipit odio. Nulla non rhoncus erat in vulputate nisi.</p></div>
<div class="abs review-card" style="left:854px"><div class="reviewer"><div class="avatar"></div><div><div class="reviewer-name">Dana Ortiz</div><div class="stars">★★★★★</div></div></div><p class="review-text">“Awesome taste, fresh. Sed laoreet, arcu eu volutpat vulputate, urna nisi elementum nunc, in gravida libero arcu sit amet neque. Fusce et ultrices nisi. Suspendisse eu suscipit odio. Nulla non rhoncus erat in vulputate nisi.</p></div>
<div class="abs arrow light" style="top:1423px;left:1103px"></div>

<h2 class="abs heading section-title-dark" style="top:1628px">Our Recipes</h2>
<article class="abs recipe-card" style="left:124px">
  <div class="recipe-photo beef-rice" role="img" aria-label="Spoonful of Mexican beef and rice with melted cheese"></div>
  <h3 class="recipe-title">One Pot Mexican<br>Beef and Rice</h3>
  <p class="recipe-text">This One Pot Mexican Beef and Rice is the ultimate weeknight diner—quick to prepare, easy to clean up, and packed with bold flavor in every bite. Ground beef is browned and simmered with beef broth, sweet corn, and Los Brava salsa, then combined with instant rice and melted cheddar for a hearty, satisfying meal that comes together in just 30 minutes.</p>
  <div class="recipe-btn">View Recipe</div>
</article>
<article class="abs recipe-card" style="left:610px">
  <div class="recipe-photo salsa-beef" role="img" aria-label="Bowl of salsa beef over rice with avocado and greens"></div>
  <h3 class="recipe-title">Slow Cooker<br>Salsa Beef</h3>
  <p class="recipe-text">This Slow Cooker Salsa Beef is a weeknight lifesaver that’s equal parts hearty, flavorful, and hands-off. Just a handful of ingredients—including ground beef, onions, bell peppers, and bold seasonings—come togethe in the slow cooker for a dish that practically makes itself.</p>
  <div class="recipe-btn">View Recipe</div>
</article>

<h2 class="abs heading section-title-dark" style="top:2071px">Follow Los Brava Dip On Snapgram</h2>
<div class="abs insta-tile" style="left:0;width:159px;background:linear-gradient(#e5e5e5,#bdbdbd)" role="img" aria-label="Rice dish"></div>
<div class="abs insta-tile" style="left:167px;background:linear-gradient(#4f8f2a,#a6cf5a)" role="img" aria-label="Verde jar with green pepper"></div>
<div class="abs insta-tile" style="left:344px;background:linear-gradient(135deg,#c74a9c,#7a3fb3)" role="img" aria-label="Salsa dish"></div>
<div class="abs insta-tile" style="left:521px;background:linear-gradient(135deg,#6c9b3a,#b52a22 60%,#6a3d22)" role="img" aria-label="Red chillies"></div>
<div class="abs insta-tile" style="left:698px;background:linear-gradient(135deg,#2a2a2a,#b85a2a 50%,#2a2a2a)" role="img" aria-label="Three jars on dark table"></div>
<div class="abs insta-tile" style="left:875px;background:linear-gradient(135deg,#efe3d0,#d46a22)" role="img" aria-label="Cheesy baked dish"></div>
<div class="abs insta-tile" style="left:1052px;width:148px;background:linear-gradient(#e0e0e0,#a8a8a8)" role="img" aria-label="Grilled dish"></div>
<div class="abs arrow" style="top:2215px;left:95px"></div>
<div class="abs arrow" style="top:2215px;left:1088px"></div>

<section class="abs signup-band"></section>
<h2 class="abs heading section-title-light" style="top:2384px">Let’s Get Los Brava Dip!</h2>
<div class="abs signup-field"><span>Enter Email Address Here</span><div class="subscribe">Subscribe</div></div>

<footer>
  <div class="abs footer-brand">Los Brava</div>
  <div class="abs footer-divider" style="left:321px"></div>
  <div class="abs footer-divider" style="left:536px"></div>
  <div class="abs footer-divider" style="left:730px"></div>
  <div class="abs footer-divider" style="left:925px"></div>
  <div class="abs footer-head" style="left:356px">CONTACT US</div>
  <ul class="abs footer-list" style="left:356px;top:2641px">
    <li class="footer-item" style="color:var(--red)"><span class="icon-dot"></span>support@losbravadip.example</li>
    <li class="footer-item"><span class="icon-dot"></span>555-014-2297</li>
  </ul>
  <div class="abs footer-head" style="left:591px">MAIN LINKS</div>
  <ul class="abs footer-list" style="left:591px"><li>Featured Product</li><li>Where to Buy</li><li>Recipes</li><li>About</li><li>Reviews</li></ul>
  <div class="abs footer-head" style="left:777px">QUICK LINKS</div>
  <ul class="abs footer-list" style="left:777px"><li>Privacy Policy</li><li>Shipping Policy</li><li>Terms and Conditions</li></ul>
  <div class="abs footer-head" style="left:985px">FOLLOW US</div>
  <ul class="abs footer-list" style="left:985px;top:2641px">
    <li class="footer-item"><span class="icon-dot"></span>Friendbook</li>
    <li class="footer-item"><span class="icon-dot"></span>Linkwork</li>
    <li class="footer-item"><span class="icon-dot"></span>Snapgram</li>
  </ul>
  <div class="abs bottom-bar">© Los Brava Dip. 2025 All Rights Reserved</div>
</footer>

</body>
</html>
```